Unique Business Card Design

Unique Business Card design for our orthotic and prosthetic company. Our logo is on our website, color is light blue. Unique shape (artificial leg shaped, vertical, etc..) preferred. Logo, business name, individual name and basic demographics needed.

Industry/Entity Type

Business

Contact Information for Business Card

Logo, Industry, Phone # Logo, "Prosthetic & Orthotic Services" Place to add individual name and contact info

Colors
cee9f5

Requirements
Must have
• The icon must be there, placement of "Prosthetic & Orthotic Services" can be moved
Nice to have
• Like the mix of light blue, and a little darker blue. One design included the icons from my website which was a nice touch

```html
<!DOCTYPE html>
<html lang="en">
<head>
<meta charset="utf-8">
<title>Limbwell Inc. Business Card</title>
<link rel="stylesheet" href="https://fonts.googleapis.com/css2?family=Montserrat:wght@400;500;700&family=Pinyon+Script&display=swap">
<style>
  :root {
    --brand-blue: #1a62b0;
    --light-blue: #cee9f5;
    --bubble-blue: #9cc6ea;
    --card-white: #ffffff;
    --backdrop: #2b2b2d;
    --text-white: #ffffff;
  }
  * { margin: 0; padding: 0; box-sizing: border-box; }
  html, body {
    width: 1200px; height: 900px; overflow: hidden;
    background: var(--backdrop);
    font-family: "Montserrat", sans-serif;
  }
  .card {
    position: absolute;
    width: 560px; height: 320px;
    border-radius: 22px;
    background: var(--card-white);
    overflow: hidden;
  }
  .card-front { left: 60px; top: 110px; }
  .card-back { left: 580px; top: 470px; }

  /* front */
  .front-brand {
    position: absolute; left: 170px; top: 62px;
    display: flex; align-items: center; gap: 18px;
  }
  .brand-dot {
    width: 110px; height: 110px; border-radius: 50%;
    background: var(--brand-blue);
    flex-shrink: 0;
  }
  .brand-name {
    color: var(--brand-blue);
    font-weight: 700;
    font-size: 26px;
    letter-spacing: 0.5px;
    white-space: nowrap;
  }
  .service {
    position: absolute;
    display: flex; flex-direction: column; align-items: center; gap: 10px;
    color: var(--brand-blue);
    font-weight: 700; font-size: 13px; letter-spacing: 0.4px;
  }
  .service-icon {
    width: 54px; height: 54px; border-radius: 50%;
    background: radial-gradient(circle at 40% 35%, #ffffff 0%, var(--light-blue) 40%, var(--bubble-blue) 100%);
    border: 1px solid var(--bubble-blue);
  }
  .service-orthotics { left: 50px; top: 218px; }
  .service-prosthetics { left: 220px; top: 200px; }
  .service-vascular { left: 400px; top: 182px; }

  /* back */
  .back-top { position: absolute; inset: 0 0 auto 0; height: 176px; }
  .back-brand-dot {
    position: absolute; left: 32px; top: 38px;
    width: 112px; height: 112px; border-radius: 50%;
    background: var(--brand-blue);
  }
  .back-brand-name {
    position: absolute; left: 164px; top: 58px;
    color: var(--brand-blue); font-weight: 700; font-size: 32px; letter-spacing: 0.5px;
  }
  .back-brand-rule {
    position: absolute; left: 164px; top: 102px;
    width: 340px; height: 3px; background: var(--brand-blue);
  }
  .tagline {
    position: absolute; left: 190px; top: 106px;
    color: var(--brand-blue);
    font-family: "Pinyon Script", cursive;
    font-size: 24px;
  }
  .rule-thin {
    position: absolute; left: 0; right: 0; top: 178px; height: 3px;
    background: var(--brand-blue);
  }
  .band {
    position: absolute; left: 0; right: 0; top: 187px; bottom: 0;
    background: var(--brand-blue);
    color: var(--text-white);
  }
  .person { position: absolute; left: 32px; top: 16px; }
  .person-name { font-weight: 700; font-size: 24px; line-height: 1.1; }
  .person-title { font-size: 15px; margin-top: 2px; margin-left: 36px; }
  .address { margin-top: 14px; margin-left: 70px; font-size: 15px; line-height: 1.3; }
  .divider {
    position: absolute; left: 300px; top: 14px; width: 1.5px; height: 104px;
    background: var(--text-white);
  }
  .contact-list {
    position: absolute; left: 316px; top: 12px;
    list-style: none; font-size: 14px; line-height: 21px;
  }
  .contact-list li { display: flex; align-items: center; gap: 10px; }
  .contact-list svg { width: 12px; height: 12px; flex-shrink: 0; }
  .web strong { font-weight: 700; }
</style>
</head>
<body>

<section class="card card-front">
  <div class="front-brand">
    <div class="brand-dot"></div>
    <span class="brand-name">LIMBWELL INC.</span>
  </div>
  <div class="service service-orthotics">
    <div class="service-icon" role="img" aria-label="Orthotics service icon: knee joint"></div>
    <span>ORTHOTICS</span>
  </div>
  <div class="service service-prosthetics">
    <div class="service-icon" role="img" aria-label="Prosthetics service icon: standing figure"></div>
    <span>PROSTHETICS</span>
  </div>
  <div class="service service-vascular">
    <div class="service-icon" role="img" aria-label="Vascular service icon: wheelchair"></div>
    <span>VASCULAR</span>
  </div>
</section>

<section class="card card-back">
  <div class="back-top">
    <div class="back-brand-dot"></div>
    <span class="back-brand-name">LIMBWELL INC.</span>
    <div class="back-brand-rule"></div>
    <span class="tagline">Prosthetic &amp; Orthotic Services</span>
  </div>
  <div class="rule-thin"></div>
  <div class="band">
    <div class="person">
      <div class="person-name">Mira Solberg</div>
      <div class="person-title">Orthotist/Prosthetist</div>
      <div class="address">2260 Harbor Ave.<br>Brooklyn, NY 11235</div>
    </div>
    <div class="divider"></div>
    <ul class="contact-list">
      <li>
        <svg viewBox="0 0 12 12"><rect x="3" y="0.5" width="6" height="11" rx="1.2" fill="none" stroke="#fff" stroke-width="1.2"/><circle cx="6" cy="9.5" r="0.7" fill="#fff"/></svg>
        555-0142-388
      </li>
      <li>
        <svg viewBox="0 0 12 12"><path d="M2.5 1 L4.5 1 L5.3 3.6 L4 4.6 Q5 7 7.4 8 L8.4 6.7 L11 7.5 L11 9.5 Q10.5 11 9 11 Q1 10 1 3 Q1 1.5 2.5 1 Z" fill="#fff"/></svg>
        555.210.4400
      </li>
      <li>
        <svg viewBox="0 0 12 12"><rect x="2" y="5" width="8" height="5" rx="1" fill="#fff"/><rect x="3.5" y="1.5" width="5" height="3.5" fill="none" stroke="#fff" stroke-width="1"/></svg>
        555.210.4411
      </li>
      <li>
        <svg viewBox="0 0 12 12"><rect x="1" y="2.5" width="10" height="7" rx="1" fill="none" stroke="#fff" stroke-width="1.2"/><path d="M1.5 3 L6 6.5 L10.5 3" fill="none" stroke="#fff" stroke-width="1.1"/></svg>
        msolberg@limbwellinc.com
      </li>
      <li class="web">
        <svg viewBox="0 0 12 12"><circle cx="6" cy="6" r="5" fill="none" stroke="#fff" stroke-width="1.1"/><ellipse cx="6" cy="6" rx="2.2" ry="5" fill="none" stroke="#fff" stroke-width="0.9"/><path d="M1 6 H11" stroke="#fff" stroke-width="0.9"/></svg>
        <span>www.<strong>limbwellinc</strong>.com</span>
      </li>
    </ul>
  </div>
</section>

</body>
</html>
```